KorvaNest - Home Income and Business Resources Platform

I am looking for a website template for a multi-purposed website. This website will feature:

1.) Website Directory with Ratings & comments on listings
2.) Company Blog
3.) Homepage with Content (see files for homepage mock)

I would like the Design to have a default width 1170px (wider then normal)

Of course I am looking for Pages for Listings to be designed.

Great looking BLOG Layout: http://journal.plimworks.example/html/blog.html

I would like 4 Versions of a Website Directory Listing "Box"
1.) Basic Listing Box
2.) Sponsored Listing Box
3.) Recommended Listing Box
4.) Stay Away From Listing Box

Information on the Listing Page (Like on a Category Page)
Site Name, Site URL, Website Image, # of Views, Rating and # of Comments

Information on the Listing Details Page:
Same as ABOVE + About website Description, Vornic Score, Category Information

Decent looking examples is here: https://samples.trevolin.example/directory/computers/ and http://www.zqrankhub.example/.

I will include some sketches and screenshots of things I like/looking for. As designers,you have creative freedom and are encouraged to show this. This is Phase one of this project and winning designer is guaranteed to have future work for this project.

Target Market(s)

Directory, business, websites

Industry/Entity Type

Business

Coding

Coded - Design and coding required

Number of Pages Required

5+ page

Font styles to use
Sans Serif

Colors

Designer to choose colors to be used in the design.

Requirements
Must have
• Professional yet clean look. The use of Icons & images
• Unique Look
Should not have
• Any exact copies of any examples I provided

```html
<!DOCTYPE html>
<html lang="en">
<head>
<meta charset="utf-8">
<title>KorvaNest – Home Income and Business Resources</title>
<link rel="stylesheet" href="https://fonts.googleapis.com/css2?family=Open+Sans:wght@400;600;700&family=Figtree:wght@400;600;700;800&display=swap">
<style>
  :root{
    --orange:#e8792a;
    --blue:#0c5c9c;
    --white:#ffffff;
    --text:#4a4a4a;
    --line:#dcdcdc;
    --ad-bg:#14b4ea;
    --ad-deep:#0f9fd4;
  }
  *{box-sizing:border-box;margin:0;padding:0}
  html,body{width:1200px;height:830px;overflow:hidden}
  body{position:relative;background:linear-gradient(135deg,#ededef 0%,#e3e3e6 50%,#ececee 100%);font-family:"Figtree",sans-serif;color:var(--text)}

  .site-header{position:absolute;left:0;top:0;width:1200px;height:61px;background:var(--white);box-shadow:0 1px 3px rgba(0,0,0,.06)}
  .brand{position:absolute;left:74px;top:8px;font-family:"Open Sans",sans-serif;font-size:35px;color:var(--orange);font-weight:400;letter-spacing:.3px}
  .brand b{font-weight:700}
  .header-icons{position:absolute;left:972px;top:17px;display:flex;gap:26px}
  .header-icons svg{width:24px;height:24px}

  .hero{position:absolute;left:73px;top:61px;width:774px;height:265px;overflow:hidden}
  .hero-photo{position:absolute;inset:0;background:linear-gradient(180deg,#55595f 0%,#6f7277 45%,#8a8680 70%,#5a5c60 100%)}
  .hero-shade{position:absolute;inset:0;background:rgba(40,42,46,.25)}
  .hero-content{position:absolute;left:0;right:0;top:42px;text-align:center;color:var(--white);font-family:"Open Sans",sans-serif}
  .hero-title{font-size:34px;font-weight:700;letter-spacing:1px;line-height:42px}
  .hero-text{width:420px;margin:12px auto 0;font-size:14.3px;line-height:21px}
  .hero-button{display:inline-block;margin-top:22px;width:125px;height:37px;line-height:37px;background:#efefef;color:#444;font-weight:700;font-size:15px;letter-spacing:.5px}

  .sponsors{position:absolute;left:870px;top:48px;width:198px;height:457px;background:var(--white);box-shadow:0 1px 3px rgba(0,0,0,.05)}
  .sponsors-title{position:absolute;top:26px;left:0;right:0;text-align:center;color:var(--blue);font-weight:800;font-size:16.5px}
  .sponsor{position:absolute;left:18px;width:163px;text-align:center}
  .sponsor-box{height:54px;border:1px solid var(--line);display:flex;align-items:center;justify-content:center;gap:6px;font-weight:700;font-size:12px;color:var(--blue)}
  .sponsor-dot{width:10px;height:10px;border-radius:50%;background:var(--blue)}
  .sponsor-name{margin-top:10px;font-size:11.5px;color:#222}

  .promo{position:absolute;left:869px;top:533px;width:200px;height:200px;background:linear-gradient(160deg,var(--ad-bg) 0%,var(--ad-deep) 100%)}

  .feature{position:absolute;top:340px;width:251px;height:400px}
  .feature-shape{position:absolute;inset:0}
  .feature-head{position:absolute;left:0;top:0;width:251px;height:92px;border-bottom:1px solid var(--line);display:flex;align-items:center}
  .feature-icon{width:78px;height:50px;display:flex;align-items:center;justify-content:center;border-right:1px solid var(--line)}
  .feature-icon svg{width:40px;height:40px}
  .feature-title{padding-left:14px;color:var(--blue);font-size:17px;line-height:20px}
  .feature-title strong{font-weight:800;display:block}
  .feature-title span{font-weight:400;display:block}
  .feature-body{position:absolute;left:24px;top:114px;width:204px;font-size:12px;line-height:20px;text-align:justify;color:var(--text)}

  .site-footer{position:absolute;left:0;top:772px;width:1200px;text-align:center;font-size:13px;color:#555}
</style>
</head>
<body>

<header class="site-header">
  <div class="brand"><b>Korva</b>Nest</div>
  <div class="header-icons">
    <svg viewBox="0 0 24 24" aria-label="Home"><path d="M12 3 2 12h3v8h5v-5h4v5h5v-8h3z" fill="#a9a9a9"/></svg>
    <svg viewBox="0 0 24 24" aria-label="Search"><circle cx="10" cy="10" r="6.5" fill="none" stroke="#a9a9a9" stroke-width="2.6"/><path d="M15 15l6 6" stroke="#a9a9a9" stroke-width="3" stroke-linecap="round"/></svg>
  </div>
</header>

<section class="hero">
  <div class="hero-photo" role="img" aria-label="Businessman in a suit with a city skyline at dusk"></div>
  <div class="hero-shade"></div>
  <div class="hero-content">
    <h1 class="hero-title">ABOUT KORVANEST</h1>
    <p class="hero-text">It is a long established fact that a reader will be distracted by the readable content of a page when looking at its layout. The point of using Lorem Ipsum.</p>
    <span class="hero-button">READ MORE</span>
  </div>
</section>

<aside class="sponsors">
  <h2 class="sponsors-title">OUR SPONSOR</h2>
  <div class="sponsor" style="top:71px"><div class="sponsor-box"><span class="sponsor-dot"></span>Harbor Loom</div><div class="sponsor-name">Harbor Loom</div></div>
  <div class="sponsor" style="top:164px"><div class="sponsor-box">Skyline Trade</div><div class="sponsor-name">Skyline Trade</div></div>
  <div class="sponsor" style="top:260px"><div class="sponsor-box"><span class="sponsor-dot"></span>Hueview</div><div class="sponsor-name">Hueview</div></div>
  <div class="sponsor" style="top:360px"><div class="sponsor-box">Trade Signal</div><div class="sponsor-name">Trade Signal</div></div>
</aside>

<div class="promo" role="img" aria-label="Third-party advertisement banner"></div>

<article class="feature" style="left:73px">
  <svg class="feature-shape" viewBox="0 0 251 400" preserveAspectRatio="none"><path d="M0 0H251V390C200 392 175 378 130 388C85 398 45 400 0 392Z" fill="#fff"/></svg>
  <div class="feature-head">
    <div class="feature-icon"><svg viewBox="0 0 40 40"><rect x="12" y="3" width="20" height="27" rx="2" fill="#e9eef3" stroke="#2b5a86" stroke-width="1.5"/><path d="M16 13l6-5 6 5v6H16z" fill="#f6c244" stroke="#2b5a86" stroke-width="1.2"/><path d="M16 23h12M16 26h9" stroke="#2b5a86" stroke-width="1.2"/><circle cx="11" cy="30" r="4" fill="#bfe3f2" stroke="#2b5a86" stroke-width="1.5"/><path d="M8 33l-4 4" stroke="#2b5a86" stroke-width="2" stroke-linecap="round"/></svg></div>
    <h3 class="feature-title"><strong>HOME INCOME</strong><span>Resource Directory</span></h3>
  </div>
  <p class="feature-body">Find what you need, when you need it.The KorvaNest website directory is your one-stop pit for anything involved in making money from home, marketing your business or finding a new opportunity. Our modern, community supported directory will help you keep upto todate with the lastest information in a sensible fashion.</p>
</article>

<article class="feature" style="left:335px">
  <svg class="feature-shape" viewBox="0 0 251 400" preserveAspectRatio="none"><path d="M0 0H251V390C200 392 175 378 130 388C85 398 45 400 0 392Z" fill="#fff"/></svg>
  <div class="feature-head">
    <div class="feature-icon"><svg viewBox="0 0 40 40"><path d="M6 18l20-10v22L6 22z" fill="#8ec4e6" stroke="#2b5a86" stroke-width="1.5"/><path d="M10 22l3 9h4l-2-8" fill="#f19a9a" stroke="#2b5a86" stroke-width="1.3"/><ellipse cx="27" cy="19" rx="3" ry="11" fill="#d8ecf8" stroke="#2b5a86" stroke-width="1.5"/><path d="M33 12l4-3M34 19h4M33 26l4 3" stroke="#2b5a86" stroke-width="1.3"/></svg></div>
    <h3 class="feature-title" style="padding-left:20px"><strong>ADVERTISING</strong><span>Benefits</span></h3>
  </div>
  <p class="feature-body">Everyone needs to advertise and we know just how to get your offer out to the right people. We have many methods including: Text ads, E-mail, Display, newsletter and even some old school methods available to make your next campaign a success. Advertise a website, a link text, full page circular or a small display ad and get results. Every advertiser recieves a dedicated account manager that will handle everything for You.</p>
</article>

<article class="feature" style="left:596px">
  <svg class="feature-shape" viewBox="0 0 251 400" preserveAspectRatio="none"><path d="M0 0H251V390C200 392 175 378 130 388C85 398 45 400 0 392Z" fill="#fff"/></svg>
  <div class="feature-head">
    <div class="feature-icon" style="width:90px"><svg viewBox="0 0 40 40"><rect x="16" y="4" width="20" height="12" rx="1" transform="rotate(-25 26 10)" fill="#7fd3b5" stroke="#2b5a86" stroke-width="1.4"/><text x="24" y="15" font-size="8" fill="#2b5a86" font-family="sans-serif" transform="rotate(-25 26 10)">$</text><path d="M4 28h8c4-3 10-4 14-4l6-2c2 0 2 3 0 4l-12 6H8" fill="#f6c244" stroke="#2b5a86" stroke-width="1.4"/><rect x="2" y="26" width="4" height="9" fill="#2b5a86"/></svg></div>
    <h3 class="feature-title" style="padding-left:16px"><strong>EARNING WITH</strong><span>KorvaNest</span></h3>
  </div>
  <p class="feature-body">Join KorvaNest and start earning money. When you share KorvaNest and lock in an advertiser or premium listing, we reward you. Build a downline at any of our listed sites when you share KorvaNest with NO extra work. Its all done for you.We also offer a revenue share program for true supporters of our mission.</p>
</article>

<footer class="site-footer">Copyrights @ 2017 All Rights Reserved</footer>

</body>
</html>
```